Local Roofing/Construction company business needs new biz card design

We need a new business card design, current cards are from the start of this operation and generic at best. We are a local Construction Company (General Contractor) with a majority of our work originating from insurance claims-exterior finish work is the main focus (Roofs-Siding-Gutters etc). Heavily involved with homeowners and the low ball offers they receive from insurance company's after a insurable event takes place. I have attached some of our original logo file(s) below.

```html
<!DOCTYPE html>
<html lang="en">
<head>
<meta charset="utf-8">
<title>Halvern Build – Business Card</title>
<link rel="stylesheet" href="https://fonts.googleapis.com/css2?family=Michroma&family=Manrope:wght@400;500;800&display=swap">
<style>
  :root {
    --bg: #d3d4d6;
    --green: #62b873;
    --green-deep: #4fa462;
    --ink: #0e1c1f;
    --text: #1d2326;
    --paper: #ffffff;
  }
  * { margin: 0; padding: 0; box-sizing: border-box; }
  html, body { width: 900px; height: 1200px; overflow: hidden; background: var(--bg); }
  .canvas { position: relative; width: 900px; height: 1200px; }

  .card { position: absolute; left: 135px; width: 630px; height: 358px; }
  .card-front {
    top: 214px;
    background: var(--green);
    display: flex; align-items: center; justify-content: center; gap: 14px;
  }
  .card-front .brand-name {
    font-family: "Manrope", sans-serif; font-weight: 800;
    font-size: 46px; letter-spacing: 1px; color: var(--ink); line-height: 1;
    text-transform: uppercase;
  }
  .brand-square { width: 34px; height: 34px; background: var(--ink); }

  .card-back { top: 628px; background: var(--paper); }
  .back-brand {
    position: absolute; left: 272px; top: 731px; width: 152px; height: 154px;
    display: flex; flex-direction: column; justify-content: center; align-items: center; gap: 10px;
  }
  .back-brand .brand-square { width: 40px; height: 40px; background: var(--green); }
  .back-brand .brand-name {
    font-family: "Manrope", sans-serif; font-weight: 800; color: var(--green);
    font-size: 27px; line-height: 1.05; text-align: center; text-transform: uppercase;
  }
  .divider { position: absolute; left: 449px; top: 731px; width: 1.5px; height: 152px; background: var(--text); }

  .contact { position: absolute; left: 474px; top: 727px; color: var(--text); font-family: "Manrope", sans-serif; }
  .person-name { font-family: "Michroma", sans-serif; color: var(--green); font-size: 18px; letter-spacing: 1px; line-height: 1.2; }
  .person-role { font-size: 14.5px; font-weight: 500; letter-spacing: 0.6px; margin-top: 4px; }
  .contact-list { list-style: none; margin-top: 24px; }
  .contact-list li { display: flex; align-items: center; gap: 5px; height: 24.5px; font-size: 14.5px; font-weight: 500; letter-spacing: 0.4px; }
  .contact-list li.phone { letter-spacing: 3px; }
  .contact-list svg { width: 12px; height: 12px; fill: var(--green); flex: none; }
</style>
</head>
<body>
<div class="canvas">
  <section class="card card-front" aria-label="Card front">
    <span class="brand-square"></span>
    <span class="brand-name">Halvern Build</span>
  </section>

  <section class="card card-back" aria-label="Card back"></section>
  <div class="back-brand">
    <span class="brand-square"></span>
    <span class="brand-name">Halvern<br>Build</span>
  </div>
  <div class="divider"></div>
  <div class="contact">
    <h1 class="person-name">DALTON J MERCER</h1>
    <p class="person-role">Chief Executive Officer</p>
    <ul class="contact-list">
      <li class="phone"><svg viewBox="0 0 24 24"><path d="M6.6 10.8a15 15 0 0 0 6.6 6.6l2.2-2.2a1 1 0 0 1 1-.25 11.4 11.4 0 0 0 3.6.57 1 1 0 0 1 1 1V20a1 1 0 0 1-1 1A17 17 0 0 1 3 4a1 1 0 0 1 1-1h3.5a1 1 0 0 1 1 1c0 1.25.2 2.45.57 3.57a1 1 0 0 1-.25 1z"/></svg>555-310-2841</li>
      <li class="phone"><svg viewBox="0 0 24 24"><path d="M7 1h10a2 2 0 0 1 2 2v18a2 2 0 0 1-2 2H7a2 2 0 0 1-2-2V3a2 2 0 0 1 2-2zm0 3v14h10V4zm5 15.5a1 1 0 1 0 0 2 1 1 0 0 0 0-2z"/></svg>555-472-9063</li>
      <li><svg viewBox="0 0 24 24"><path d="M2 5h20v14H2zm2 2v.5l8 5 8-5V7zm0 3v7h16v-7l-8 5z"/></svg>info@halvernbuild.com</li>
      <li><svg viewBox="0 0 24 24"><path d="M12 2a10 10 0 1 0 0 20 10 10 0 0 0 0-20zm6.9 6h-3a15 15 0 0 0-1.3-3.9A8 8 0 0 1 18.9 8zM12 4a13 13 0 0 1 1.9 4h-3.8A13 13 0 0 1 12 4zM4.3 14a8 8 0 0 1 0-4h3.4a16 16 0 0 0 0 4zm.8 2h3a15 15 0 0 0 1.3 3.9A8 8 0 0 1 5.1 16zm3-8h-3a8 8 0 0 1 4.3-3.9A15 15 0 0 0 8.1 8zM12 20a13 13 0 0 1-1.9-4h3.8A13 13 0 0 1 12 20zm2.3-6H9.7a14 14 0 0 1 0-4h4.6a14 14 0 0 1 0 4zm.3 5.9a15 15 0 0 0 1.3-3.9h3a8 8 0 0 1-4.3 3.9zM16.3 14a16 16 0 0 0 0-4h3.4a8 8 0 0 1 0 4z"/></svg>halvernbuild.com</li>
    </ul>
  </div>
</div>
</body>
</html>
```